Website Redesign for a faith-based, not-for-profit health and human services organization

New website design for the Harvest Hope Outreach House.
- Current site: www.hhohbriel.org -
We are looking for a nice clean, simple, friendly-yet-elegant website layout.
Colors are #f5eed5 (cream), #FFFFFF (white), and all logo colors.
Design a layout for home page
Design a layout for general layouts
-layout only no html needed (preferably a high res PSD file format) -
Main menu should be along top with side navigation for submenu, no side menu on home page.
Also would be open to seeing some updated colors on the logo design, currently the colors are slightly outdated. The Vine of Plenty quilt design fits the organization’s mission and the rural farming / Amish-Mennonite-Brethren community around us.

ADDITIONAL PAGES AND MENU STRUCTURE ON NEW SITE

- How to Help
... Volunteer
... Donate Time
... Donate Money
... Donate Supplies
... Current Needs

- Programs

- News & Events
... Upcoming Events
... Upcoming Fundraisers
... Newsletter

- Our Partners

- About Us
... Overview
... Mission
... Staff Directory
... Board of Directors
... Annual Reports

- Contact

Our annual special event is Gather at the Hearth and should be integrated into the home page - see attached logos and banner

Websites with elements we like (from organizations doing similar work), each for a different reason....

1. http://www.kinbridgeroutes.org
Good design, color, clarity on this site. Multi-dimensional, photos...easy interaction, etc.

2. http://endemptyplates.org
Quite simple, nothing fancy, but some good basic stuff here, and pretty easy to navigate...

3. http://www.townfolkhub.org
Intrigued by the bulletin board design and the way they have their programs broken down to show impact, needs, etc. It has a lot of good information, but is really too verbose, some of the print is too small, etc. Not perfect, but some interesting design elements.

4. http://sharedlarder.org
Site is boring and not very well designed, but it has some of the features that we would like to see at the top, donations, partners, etc.

5. http://www.bellmerefoodshelf.org
Too many listings on the sidebar - needs to be cleaner & simpler, but a lot of good information and we like the way they show volunteer photos on the Thanks to Our Helpers page...

About
Harvest Hope Outreach House ("HHOH" or “the Center”) is a faith-based non-for-profit health and human services organization that exists as an outreach of and for the Ordell-Bray Area School District.
Tagline: Mercy at Work (we work to serve the needs of the ‘least of these’ with compassion).

Mission
Our mission is to see lives transformed and the community enhanced by encouraging the oppressed, defending the cause of the weak and maintaining the rights of the poor - bringing together the resources of a caring community as a demonstration of the good news of Christ.

Company Overview
Harvest Hope Outreach House works closely with the community in which it serves. A tremendous value is placed upon the partnerships that have formed with caring people within the community and with organizations that share the goal of bringing together resources to help those who need it most. Individuals, volunteers, churches, corporations, foundations, and government sources all pull together to help make our mission possible.

Since 1996 the Harvest Hope Outreach House has collaboratively worked to see our community enhanced, adapting programs and services to meet the changing needs of the community.

Target Market(s)

people needing assistance in local community

Industry/Entity Type

Government

Requirements
Must have
• Good social button integration
Should not have
• No Find Us page like old website it is not needed

```html
<!DOCTYPE html>
<html lang="en">
<head>
<meta charset="utf-8">
<title>Harvest Hope Outreach House</title>
<link rel="stylesheet" href="https://fonts.googleapis.com/css2?family=Sorts+Mill+Goudy&family=Arimo:wght@400;700&display=swap">
<style>
:root{
  --maroon:#7a1428;
  --maroon-text:#7d1a2b;
  --cream:#f5eed5;
  --gold:#b8860b;
  --gold-band:#c28a0e;
  --green:#0e4a26;
  --green-dark:#0a3a1d;
  --white:#ffffff;
  --ink:#1e1e1e;
  --grey-box:#e3e3e3;
  --grey-frame:#dcdcdc;
}
*{box-sizing:border-box;margin:0;padding:0}
html,body{width:1200px;height:1150px;overflow:hidden}
body{background:var(--maroon);font-family:"Arimo",Arial,sans-serif;color:var(--ink);position:relative}
.page{position:absolute;left:102px;top:0;width:996px;height:1150px;background:var(--white)}
.header{position:absolute;left:0;top:0;width:996px;height:206px}
.header svg{position:absolute;left:0;top:0}
.brand{position:absolute;left:14px;top:18px;display:flex;align-items:center;gap:14px}
.brand-mark{width:90px;height:90px;background:var(--maroon-text)}
.brand-name{font-family:"Sorts Mill Goudy",serif;color:var(--gold);font-size:24px;line-height:23px}
.donate{position:absolute;left:542px;top:29px;width:142px;height:43px;border-radius:10px;background:linear-gradient(#ffe56a,#f6bd10);border:1px solid #d19a08;font-family:"Sorts Mill Goudy",serif;font-size:26px;color:#3a2a08;text-align:center;line-height:42px;letter-spacing:1px}
.call{position:absolute;left:468px;top:84px;font-family:"Sorts Mill Goudy",serif;font-size:20px;color:var(--gold)}
.call strong{font-family:"Arimo",Arial,sans-serif;font-weight:400;font-size:24px;color:var(--maroon-text)}
.connect{position:absolute;left:806px;top:18px}
.connect h3{font-family:"Sorts Mill Goudy",serif;font-weight:400;font-size:26px;color:var(--gold)}
.social{display:flex;gap:10px;margin-top:6px}
.social span{font-size:12px;color:var(--gold);display:flex;align-items:center;gap:4px}
.social i{display:inline-block;width:12px;height:12px;background:var(--gold)}
.nav{position:absolute;left:128px;top:168px;display:flex;height:38px}
.nav a{color:var(--white);font-weight:700;font-size:14px;text-decoration:none;line-height:38px;text-align:center;border-right:1px solid #07321a;border-left:1px solid #1a5c34;white-space:nowrap}
.nav a:first-child{border-left:0}.nav a:last-child{border-right:0}
.slider{position:absolute;left:18px;top:206px;width:960px;height:354px;background:var(--grey-frame);box-shadow:0 22px 18px -14px rgba(0,0,0,.35)}
.slide-photo{position:absolute;left:9px;top:8px;width:942px;height:337px;background:linear-gradient(160deg,#8a5a4a 0%,#b8a89a 35%,#e8e8e8 60%,#7a8a6a 100%)}
.caption{position:absolute;left:26px;top:98px;width:466px;height:100px;background:rgba(255,255,255,.55);font-family:"Sorts Mill Goudy",serif;color:var(--maroon-text);padding:6px 0 0 8px}
.caption .l1{font-size:34px;line-height:34px}
.caption .l2{font-size:30px}
.caption .l2 b{font-size:56px;color:var(--green);font-weight:700;line-height:50px}
.dots{position:absolute;left:9px;top:304px;width:226px;height:41px;background:rgba(0,0,0,.55);display:flex;gap:10px;padding:13px 0 0 18px}
.dots i{width:15px;height:15px;border-radius:50%;background:#f7edd0}
.dots i.on{background:#a0142e}
.main{position:absolute;left:20px;top:0;width:680px;height:1050px}
.main > *{position:absolute}
h2{font-family:"Sorts Mill Goudy",serif;font-weight:400;color:var(--gold);font-size:29px;letter-spacing:.5px;line-height:32px}
p{font-size:12.5px;line-height:18px}
.about-title{left:0;top:606px}
.about-photo{left:3px;top:652px;width:181px;height:226px;background:var(--grey-box);padding:6px}
.about-photo div{width:100%;height:100%;background:linear-gradient(180deg,#8b8f87,#a9a49a 60%,#6f8a4c)}
.about-text{left:194px;top:651px;width:482px;text-align:justify}
.more{font-size:12.5px;font-weight:700;color:var(--green);text-decoration:none;right:4px;line-height:16px}
.more-about{top:875px}
.rule{left:0;top:901px;width:680px;border-top:1px solid #d8d8d8}
.mission-title{left:0;top:907px}
.mission-text{left:8px;top:943px;width:666px;text-align:justify}
.mission-text::before{content:"\201C";position:absolute;left:-18px;top:-4px;font-size:30px;color:#b5b5b5;font-family:Georgia,serif}
.mission-text .end{font-size:30px;color:#b5b5b5;font-family:Georgia,serif;line-height:0;vertical-align:-12px}
.more-mission{top:1005px}
.newsletter{position:absolute;left:736px;top:615px;width:243px;height:120px;border-radius:12px;background:linear-gradient(var(--green-dark),#17592f);padding:10px 0 0 17px}
.newsletter h3,.events h3{font-family:"Sorts Mill Goudy",serif;font-weight:400;font-size:25px;line-height:30px}
.newsletter h3{color:var(--white)}
.newsletter .field{margin-top:7px;width:200px;height:28px;background:#f0f0f0;font-size:11px;color:#888;padding:7px 8px}
.newsletter .btn{position:absolute;right:23px;top:86px;padding:3px 6px;border-radius:5px;background:linear-gradient(#f6edcc,#c8ae72);font-size:12.5px;color:#222}
.events{position:absolute;left:736px;top:765px;width:240px;height:258px;border-radius:6px;background:var(--grey-box);padding:6px 0 0 16px}
.events h3{color:#222}
.event{display:flex;gap:8px;margin:10px 12px 0 -8px;padding-bottom:4px;border-bottom:1px solid #fff;height:56px}
.event + .event{margin-top:3px}
.event:last-of-type{border-bottom:0}
.thumb{width:46px;height:41px;flex:none;background:linear-gradient(#cfcfcf,#8c8c8c);border:2px solid #fff}
.event b{display:block;font-size:12.5px;line-height:16px;color:#333}
.event span{font-size:12px;line-height:16px;color:#333}
.events .btn{position:absolute;right:7px;bottom:7px;background:var(--green);color:#fff;font-weight:700;font-size:12.5px;padding:2px 5px;border-radius:3px}
.footer{position:absolute;left:0;top:1055px;width:996px;height:95px;background:var(--green)}
.footer p{position:absolute;left:23px;top:14px;color:#fff;font-size:12.5px;line-height:21px;word-spacing:2px}
.event-brand{position:absolute;left:806px;top:32px;display:flex;align-items:center;gap:6px;font-family:"Sorts Mill Goudy",serif;font-size:16px;color:#f5eed5;white-space:nowrap}
.event-brand i{width:14px;height:14px;background:#f5eed5}
</style>
</head>
<body>
<div class="page">
  <header class="header">
    <svg width="996" height="206" viewBox="0 0 996 206" aria-hidden="true">
      <rect width="996" height="206" fill="#f5eed5"/>
      <path d="M0 118 Q330 170 600 148 Q820 128 996 78 L996 206 L0 206 Z" fill="#c28a0e"/>
      <path d="M0 126 Q320 180 600 162 Q820 148 996 128 L996 206 L0 206 Z" fill="#0e4a26"/>
    </svg>
    <div class="brand"><span class="brand-mark"></span><span class="brand-name">Harvest Hope<br>Outreach<br>House</span></div>
    <div class="donate">Donate</div>
    <div class="call">Call us: <strong>555.014.2290</strong></div>
    <div class="connect"><h3>Connect</h3>
      <div class="social"><span><i></i>Kinfolio</span><span><i></i>Chirplet</span></div>
    </div>
    <nav class="nav">
      <a style="width:76px">Home</a><a style="width:112px">How to Help</a><a style="width:100px">Programs</a><a style="width:130px">News &amp; Events</a><a style="width:120px">Our Partners</a><a style="width:96px">About Us</a><a style="width:84px">Contact</a>
    </nav>
  </header>

  <section class="slider">
    <div class="slide-photo" role="img" aria-label="Group photo of volunteers and children in matching white shirts outside a brick building"></div>
    <div class="caption"><div class="l1">Building a Better Community</div><div class="l2">for <b>16 years!</b></div></div>
    <div class="dots"><i></i><i class="on"></i><i></i><i></i></div>
  </section>

  <main class="main">
    <h2 class="about-title">Harvest Hope Outreach House</h2>
    <div class="about-photo"><div role="img" aria-label="Entrance of the Center with green arched awning"></div></div>
    <p class="about-text"><b>Harvest Hope Outreach House</b> works closely with the community in which it serves. A tremendous amount of value is placed upon the partnerships that have formed with caring people within the community and organizations that share the goal of bringing together resources to help those who need it most. Individuals, volunteers, churches, corporations, foundations, and government sources all pull together to help make our mission possible. <b>Since 1996 Harvest Hope Outreach</b> House has collaboratively worked to see our community enhanced.<br><br>Along the bank of the river, on this side and that, will grow all kinds of trees used for food; their leaves will not wither, and their fruit will not fail. They will bear fruit every month, because their water flows from the sanctuary. Their fruit will be for food, and their leaves for medicine</p>
    <a class="more more-about">&#9656;&#9656;read more</a>
    <div class="rule"></div>
    <h2 class="mission-title">Our Mission</h2>
    <p class="mission-text">Our mission is to see lives transformed and the community enhanced by encouraging the oppressed, defending the cause of the weak and maintaining the rights of the poor by bringing together the resources of a caring community as a demonstration of the good news of Christ.<span class="end">&#8221;</span></p>
    <a class="more more-mission">&#9656;&#9656;read more</a>
  </main>

  <aside class="newsletter">
    <h3>Latest Newsletter</h3>
    <div class="field">Add Email Address To Join</div>
    <div class="btn">Subscribe</div>
  </aside>

  <aside class="events">
    <h3>Upcoming Events</h3>
    <div class="event"><div class="thumb" role="img" aria-label="Event speaker portrait"></div><div><b>January 12.03.13</b><span>simply dummy text of the print ing and typesetting industry.</span></div></div>
    <div class="event"><div class="thumb" role="img" aria-label="Event speaker portrait"></div><div><b>January 12.03.13</b><span>simply dummy text of the print ing and typesetting industry.</span></div></div>
    <div class="event"><div class="thumb" role="img" aria-label="Event speaker portrait"></div><div><b>January 12.03.13</b><span>simply dummy text of the print ing and typesetting industry.</span></div></div>
    <div class="btn">&#9656;&#9656;read more</div>
  </aside>

  <footer class="footer">
    <p>Home &nbsp;|&nbsp; How to Help &nbsp;|&nbsp; Programs &nbsp;|&nbsp; News &amp; Events &nbsp;|&nbsp; Our Partners &nbsp;|&nbsp; About Us &nbsp;|&nbsp; Contact<br>Harvest Hope Outreach House &nbsp; 48 Millrace Lane &nbsp; Briel &nbsp; OH &nbsp; 44901<br>Ph.: &nbsp;555.014.2290 &nbsp;Fax 555.014.2291</p>
    <div class="event-brand"><i></i>Gather at the Hearth</div>
  </footer>
</div>
</body>
</html>
```